Dalvick's Business Card

I need some designs for a new business card including the new logo attached. An old example of our business card is also attached to show all the data that should be included on the new design.
**I added some more examples someone had mocked up**

Contact Information for Business Card

Should include all info on other examples uploaded.

```html
<!DOCTYPE html>
<html lang="en">
<head>
<meta charset="utf-8">
<title>Dalvick's Business Card</title>
<link href="https://fonts.googleapis.com/css2?family=Montserrat:wght@500;600;800&display=swap" rel="stylesheet">
<style>
  :root {
    --brand-blue: #0b70b7;
    --brand-red: #e8202a;
    --paper: #ffffff;
    --backdrop: #e4e3e4;
  }
  * { margin: 0; padding: 0; box-sizing: border-box; }
  html, body { width: 1200px; height: 1200px; overflow: hidden; }
  body {
    background: var(--backdrop);
    font-family: "Montserrat", sans-serif;
    display: flex;
    flex-direction: column;
    align-items: center;
    justify-content: center;
    gap: 60px;
  }
  .card {
    position: relative;
    width: 840px;
    height: 480px;
    background: var(--paper);
    overflow: hidden;
    box-shadow: 0 18px 40px rgba(0,0,0,0.25);
  }

  /* Front */
  .band {
    position: absolute;
    left: 0; right: 0;
    height: 64px;
    display: flex;
    align-items: center;
    justify-content: center;
    color: var(--paper);
    font-weight: 500;
    letter-spacing: 0.03em;
    text-transform: uppercase;
  }
  .band-top { top: 0; background: var(--brand-blue); font-size: 25px; }
  .band-bottom { bottom: 0; background: var(--brand-red); font-size: 19px; }
  .notch {
    position: absolute;
    width: 0; height: 0;
    border-left: 22px solid transparent;
    border-right: 22px solid transparent;
  }
  .band-top .notch { bottom: -14px; left: 300px; border-top: 14px solid var(--brand-blue); }
  .band-bottom .notch { top: -14px; left: 430px; border-bottom: 14px solid var(--brand-red); }

  .brand {
    display: flex;
    align-items: center;
    gap: 18px;
    color: var(--brand-blue);
    font-weight: 800;
    letter-spacing: 0.01em;
    white-space: nowrap;
  }
  .brand-dot { border-radius: 50%; background: var(--brand-red); flex: none; }
  .front .brand {
    position: absolute;
    top: 50%; left: 50%;
    transform: translate(-50%, -50%);
    font-size: 86px;
  }
  .front .brand-dot { width: 70px; height: 70px; }

  /* Back */
  .back-shape { position: absolute; inset: 0; }
  .back .brand {
    position: absolute;
    top: 240px; left: 205px;
    transform: translate(-50%, -50%);
    font-size: 44px;
    gap: 10px;
  }
  .back .brand-dot { width: 34px; height: 34px; }
  .contact {
    position: absolute;
    left: 545px; top: 135px;
    width: 270px;
    color: var(--paper);
    font-weight: 500;
    white-space: nowrap;
  }
  .contact-name {
    color: var(--brand-red);
    font-weight: 800;
    font-size: 28px;
    text-transform: uppercase;
    margin-bottom: 24px;
  }
  .contact-line {
    display: flex;
    align-items: center;
    gap: 8px;
    font-size: 17px;
    margin-bottom: 8px;
  }
  .contact-line svg { width: 17px; height: 17px; flex: none; }
  .credentials {
    margin-top: 22px;
    font-size: 16px;
    line-height: 1.4;
    text-transform: uppercase;
    letter-spacing: 0.02em;
  }
</style>
</head>
<body>

  <section class="card front">
    <div class="band band-top">Serves Alder Creek, IA &amp; Surrounding Areas<span class="notch"></span></div>
    <div class="brand"><span class="brand-dot"></span>DALVICK'S</div>
    <div class="band band-bottom">Call today for all your HVAC, refrigeration &amp; plumbing needs<span class="notch"></span></div>
  </section>

  <section class="card back">
    <svg class="back-shape" viewBox="0 0 840 480" width="840" height="480">
      <path d="M404 0 C350 170 548 300 496 480 L520 480 C572 300 374 170 428 0 Z" fill="var(--brand-red)"/>
      <path d="M436 0 C382 170 580 300 528 480 L840 480 L840 0 Z" fill="var(--brand-blue)"/>
      <path d="M436 0 C382 170 580 300 528 480" fill="none" stroke="var(--paper)" stroke-width="5"/>
    </svg>
    <div class="brand"><span class="brand-dot"></span>DALVICK'S</div>
    <div class="contact">
      <p class="contact-name">Owen Dalvick</p>
      <p class="contact-line">
        <svg viewBox="0 0 24 24"><path d="M6.6 10.8a15 15 0 0 0 6.6 6.6l2.2-2.2a1 1 0 0 1 1-.25 11.4 11.4 0 0 0 3.6.57 1 1 0 0 1 1 1V20a1 1 0 0 1-1 1A17 17 0 0 1 3 4a1 1 0 0 1 1-1h3.5a1 1 0 0 1 1 1c0 1.250.2 2.450.57 3.57a1 1 0 0 1-.25 1z" fill="currentColor"/></svg>
        555.014.2290
      </p>
      <p class="contact-line">
        <svg viewBox="0 0 24 24"><path d="M2 5h20v14H2z" fill="currentColor"/><path d="M2 5l10 8 10-8" fill="none" stroke="var(--brand-blue)" stroke-width="2"/></svg>
        hvacdalvick@mailbox.com
      </p>
      <p class="credentials">Licensed &amp; Insured<br>Family Owned &amp; Operated</p>
    </div>
  </section>

</body>
</html>
```